Hello my Name is Elias Moreno. I buy and sell vintage comic books, you can refer to my instragram page qpkz.comics to get ideas and inspiration. For the front of the card I would like my company logo QPKZ Comics with a yellow and black background with the bat signal or bat emblem like on my IG page and with my info Elias Moreno as the Owner and address/ phone number, PO Box 617283, Miami, FL 33827, 305-482-6170 and that I buy and sell comics & collectables . Also feel free to be open to other ideas if you want. Im not stuck on one design. For the back of the card I would like for it to say follow me on Instagram QPKZ.Comics with the ig emblem. Also would like the card to be vertical if possible. Thanks

```html
<!DOCTYPE html>
<html lang="en">
<head>
<meta charset="utf-8">
<title>QPKZ Comics – Business Cards</title>
<link rel="stylesheet" href="https://fonts.googleapis.com/css2?family=Open+Sans:wght@400;700;800&display=swap">
<style>
  :root {
    --backdrop: #2e2f33;
    --card-yellow: #fdc814;
    --ink: #111111;
    --card-shadow: rgba(0,0,0,0.45);
  }
  * { margin: 0; padding: 0; box-sizing: border-box; }
  html, body {
    width: 1200px; height: 864px; overflow: hidden;
    background: var(--backdrop);
    font-family: "Open Sans", Arial, sans-serif;
    color: var(--ink);
  }
  .card {
    position: absolute;
    width: 600px; height: 343px;
    background: var(--card-yellow);
    box-shadow: 0 10px 24px var(--card-shadow);
  }
  .card--front { left: 200px; top: 70px; }
  .card--back  { left: 400px; top: 450px; }

  /* brand lockup */
  .brand {
    position: absolute;
    display: flex; align-items: center; gap: 12px;
  }
  .brand__dot {
    width: 58px; height: 58px; border-radius: 50%;
    background: var(--ink); flex: none;
  }
  .brand__name {
    font-weight: 800; font-size: 30px; line-height: 1.05;
    letter-spacing: 0.5px; color: var(--ink);
  }
  .card--front .brand { left: 36px; top: 118px; }
  .card--back .brand  { right: 34px; top: 78px; }

  /* front */
  .headline {
    position: absolute; right: 40px; top: 34px;
    text-align: center; font-weight: 700; line-height: 1.08;
    text-transform: uppercase;
  }
  .headline__big   { font-size: 46px; letter-spacing: 1px; }
  .headline__mid   { font-size: 38px; }
  .headline__small { font-size: 29px; }
  .follow {
    position: absolute; right: 42px; bottom: 24px;
    display: flex; align-items: center; gap: 10px;
    font-weight: 700; font-size: 15px;
  }
  .follow__square {
    width: 20px; height: 20px; border-radius: 4px; background: var(--ink);
  }

  /* back */
  .owner { position: absolute; left: 42px; top: 140px; }
  .owner__name  { font-weight: 700; font-size: 18px; }
  .owner__title { font-size: 13px; margin-top: 2px; }
  .divider {
    position: absolute; left: 0; right: 0; top: 190px;
    height: 2px; background: var(--ink);
  }
  .contact {
    position: absolute; right: 34px; bottom: 34px;
    text-align: right; font-size: 15px; line-height: 1.75;
  }
  .contact__phone { display: inline-flex; align-items: center; gap: 10px; }
  .contact__phone svg { width: 14px; height: 14px; }
</style>
</head>
<body>

<section class="card card--front" aria-label="Card front">
  <div class="brand">
    <span class="brand__dot"></span>
    <span class="brand__name">QPKZ<br>Comics</span>
  </div>
  <h1 class="headline">
    <div class="headline__big">We Buy</div>
    <div class="headline__mid">And Sell</div>
    <div class="headline__mid">Comics &amp;</div>
    <div class="headline__small">Collectables</div>
  </h1>
  <div class="follow">
    <span>Follow me on</span>
    <span class="follow__square"></span>
    <span>QPKZ.Comics</span>
  </div>
</section>

<section class="card card--back" aria-label="Card back">
  <div class="owner">
    <div class="owner__name">Elias Moreno</div>
    <div class="owner__title">Owner</div>
  </div>
  <div class="divider"></div>
  <div class="brand">
    <span class="brand__dot"></span>
    <span class="brand__name">QPKZ<br>Comics</span>
  </div>
  <div class="contact">
    <div class="contact__phone">305-482-6170
      <svg viewBox="0 0 24 24" aria-hidden="true"><path fill="#111" d="M6.6 10.8a15.1 15.1 0 0 0 6.6 6.6l2.2-2.2a1 1 0 0 1 1-.25 11.4 11.4 0 0 0 3.6.57 1 1 0 0 1 1 1V20a1 1 0 0 1-1 1A17 17 0 0 1 3 4a1 1 0 0 1 1-1h3.5a1 1 0 0 1 1 1c0 1.25.2 2.45.57 3.57a1 1 0 0 1-.25 1z"/></svg>
    </div>
    <div>PO Box 617283&nbsp;&nbsp;Miami, FL 33827</div>
  </div>
</section>

</body>
</html>
```